Trabworth Business Cards

We need a business card design for Trabworth Mining.

This is a B2B company that buys and sells large machinery tires within the coal mining industry. The design should the strong, crisp and masculine. I have uploaded the company logo and rough mock-up of what the back of the card should look like. the front of the card should have the same look/feel as the back. I need editable templates for both the front and the back of the card.

Color scheme should be grey/green/black

Contact information to include on the card:
Name: Dale Pembrose
Title: Managing Director
Phone: 555-314-2069
Address: 1187 Welford #3 Dallas, TX 75290
Email: Dale@Trabworth-example.com

I am also opening a contest for letterhead design. If you submit a business card design, please also submit a letterhead design with the same look/feel. The winner of the business card design will also will the letter head and be paid for both.

Target Market(s)

Procurement men/women in the coal mining industry

Industry/Entity Type

Coal Mining

```html
<!DOCTYPE html>
<html lang="en">
<head>
<meta charset="utf-8">
<title>Trabworth Business Cards</title>
<link rel="stylesheet" href="https://fonts.googleapis.com/css2?family=Ubuntu:wght@400;500;700&display=swap">
<style>
  :root {
    --page-bg: #e7e4e0;
    --card-bg: #2b2b2c;
    --card-edge: #232324;
    --texture-light: rgba(255, 255, 255, 0.05);
    --brand-green: #5aab2f;
    --text-white: #f2f2f2;
    --text-soft: #d9d9d9;
  }
  * { box-sizing: border-box; margin: 0; padding: 0; }
  html, body {
    width: 1200px;
    height: 900px;
    overflow: hidden;
    background: var(--page-bg);
    font-family: "Ubuntu", sans-serif;
  }
  .canvas {
    position: relative;
    width: 1200px;
    height: 900px;
  }
  .card {
    position: absolute;
    left: 353px;
    width: 489px;
    height: 279px;
    background: var(--card-bg);
    border: 1px solid var(--card-edge);
    border-radius: 2px;
    overflow: hidden;
    box-shadow: 0 2px 6px rgba(0, 0, 0, 0.18);
  }
  .card--front { top: 161px; }
  .card--back { top: 471px; }

  .texture {
    position: absolute;
    inset: 0;
  }
  .card--front .texture {
    background: radial-gradient(ellipse 75% 90% at 85% 15%, var(--texture-light), transparent 70%);
  }
  .card--back .texture {
    background: radial-gradient(ellipse 75% 90% at 12% 10%, var(--texture-light), transparent 70%);
  }

  .brand {
    position: absolute;
    display: flex;
    align-items: center;
    gap: 10px;
    color: var(--text-white);
    font-weight: 500;
    font-size: 27px;
    letter-spacing: 0.5px;
    line-height: 1;
    white-space: nowrap;
  }
  .brand__square {
    width: 22px;
    height: 22px;
    background: var(--brand-green);
    flex: none;
  }
  .card--front .brand { left: 38px; top: 60px; }
  .card--back .brand { right: 31px; top: 175px; }

  .holder {
    position: absolute;
    left: 38px;
    top: 156px;
    display: flex;
    align-items: baseline;
    color: var(--text-white);
    white-space: nowrap;
  }
  .holder__dot {
    width: 7px;
    height: 7px;
    border-radius: 50%;
    background: var(--brand-green);
    margin-right: 23px;
    align-self: center;
  }
  .holder__name { font-size: 16px; }
  .holder__title {
    font-size: 12px;
    text-transform: uppercase;
    margin-left: 4px;
  }
  .holder__title::before { content: "| "; font-size: 15px; }

  .contacts {
    position: absolute;
    left: 36px;
    top: 191px;
    list-style: none;
  }
  .contacts__item {
    display: flex;
    align-items: center;
    height: 21px;
    font-size: 13.5px;
    color: var(--text-soft);
    white-space: nowrap;
  }
  .contacts__icon {
    width: 12px;
    height: 12px;
    margin-right: 20px;
    flex: none;
  }

  .website {
    position: absolute;
    right: 31px;
    top: 222px;
    font-size: 14px;
    letter-spacing: 0.6px;
    color: var(--text-white);
  }
</style>
</head>
<body>
<main class="canvas">

  <section class="card card--front" aria-label="Business card front">
    <div class="texture" role="img" aria-label="Faint hexagon texture across the card"></div>
    <div class="brand"><span class="brand__square"></span>Trabworth Mining</div>

    <p class="holder">
      <span class="holder__dot"></span>
      <span class="holder__name">Dale Pembrose</span>
      <span class="holder__title">Managing Director</span>
    </p>

    <ul class="contacts">
      <li class="contacts__item">
        <svg class="contacts__icon" viewBox="0 0 12 12" aria-hidden="true">
          <path d="M2.2 0.8 L4.2 2.8 L3.2 4.2 Q4.4 6.8 7.8 8.8 L9.2 7.8 L11.2 9.8 L9.6 11.4 Q4.5 10.5 0.6 2.4 Z" fill="var(--brand-green)"/>
        </svg>
        555-314-2069
      </li>
      <li class="contacts__item">
        <svg class="contacts__icon" viewBox="0 0 12 12" aria-hidden="true">
          <rect x="0.8" y="2.5" width="10.4" height="7.5" fill="none" stroke="var(--brand-green)" stroke-width="1.4"/>
          <path d="M0.8 2.8 L6 6.8 L11.2 2.8" fill="none" stroke="var(--brand-green)" stroke-width="1.4"/>
        </svg>
        Dale@Trabworth-example.com
      </li>
      <li class="contacts__item">
        <svg class="contacts__icon" viewBox="0 0 12 12" aria-hidden="true">
          <path d="M6 11.5 L2.3 6.3 A4.3 4.3 0 1 1 9.7 6.3 Z" fill="var(--brand-green)"/>
          <circle cx="6" cy="4.3" r="1.6" fill="var(--card-bg)"/>
        </svg>
        1187 Welford #3 Dallas, TX 75290
      </li>
    </ul>
  </section>

  <section class="card card--back" aria-label="Business card back">
    <div class="texture" role="img" aria-label="Faint hexagon texture across the card"></div>
    <div class="brand"><span class="brand__square"></span>Trabworth Mining</div>
    <p class="website">www.Trabworth-example.com</p>
  </section>

</main>
</body>
</html>
```